Bicycle Tour Schedule on a Business Card

Need to develop a 2 side business card that highlights a series of bike tours on 1 side and a series of events on the other side.
This will be inserted into a card wallet that attaches to a cell phone and will be handed out at an expo. The card wallets are black and red so color must coordinate with both. There is a photo of the card wallets attached.

1 side needs to be devoted to Pedal Vista Trek and the others to KQR Venture events on the other. Dates and websites are very important.

Target Market(s)

Cyclists
Predominantly men ages 40+
Educated, Professionals

Industry/Entity Type

Business

Font styles to use
Serif

Requirements
Must have
• Pedal vista treks logo on 1 side and KQR Venture logo on the other side
• dates and websites clearly visible
• Design of both sides must go together.
• Must be portrait not landscape

```html
<!DOCTYPE html>
<html lang="en">
<head>
<meta charset="utf-8">
<title>Pedal Vista Treks &amp; KQR Venture – Event Cards</title>
<link href="https://fonts.googleapis.com/css2?family=Open+Sans:ital,wght@0,400;0,700;1,700&display=swap" rel="stylesheet">
<style>
  :root {
    --tour-blue: #1f5fb8;
    --tour-blue-deep: #1a4fa0;
    --tour-green: #3fb65a;
    --tour-lime: #8cc63f;
    --event-red: #d0122e;
    --event-blue: #1196cf;
    --white: #ffffff;
    --backdrop: #ece9e4;
    --card-w: 380px;
    --card-h: 665px;
  }
  * { box-sizing: border-box; margin: 0; padding: 0; }
  html, body {
    width: 1200px; height: 950px; overflow: hidden;
    background: var(--backdrop);
    font-family: "Open Sans", Arial, sans-serif;
  }
  .sheet {
    width: 1200px; height: 950px;
    display: flex; justify-content: center; align-items: center; gap: 80px;
  }
  .card {
    width: var(--card-w); height: var(--card-h);
    display: flex; flex-direction: column;
    box-shadow: 0 6px 18px rgba(0,0,0,.18);
    color: var(--white);
    text-align: center;
    overflow: hidden;
  }

  /* ---------- Tour side ---------- */
  .tour-head {
    height: 230px; background: var(--tour-blue);
    display: flex; align-items: center; justify-content: center; gap: 16px;
    padding: 0 24px;
  }
  .brand-dot {
    width: 54px; height: 54px; border-radius: 50%; flex: none;
  }
  .tour-head .brand-dot { background: var(--tour-lime); }
  .brand-name {
    font-weight: 700; font-size: 30px; line-height: 1.1; text-align: left;
  }
  .tour-head .brand-name { color: var(--white); }
  .tour-tagline {
    background: var(--white); color: var(--tour-blue-deep);
    font-weight: 700; font-style: italic; font-size: 18px; line-height: 1.3;
    padding: 16px 22px;
  }
  .tour-list {
    flex: 1; background: var(--tour-green);
    display: flex; flex-direction: column; justify-content: center; gap: 18px;
    padding: 20px 24px;
  }
  .listing-name { font-size: 19px; font-weight: 400; line-height: 1.3; }
  .listing-date { font-size: 19px; font-weight: 700; line-height: 1.3; }

  /* ---------- Event side ---------- */
  .event-head {
    height: 230px; background: var(--event-red);
    display: flex; align-items: center; justify-content: center; gap: 16px;
  }
  .event-head .brand-dot { background: var(--white); }
  .event-head .brand-name { color: var(--white); }
  .event-tagline {
    background: var(--white); color: var(--event-red);
    font-weight: 700; font-size: 19px; line-height: 1.3;
    padding: 14px 20px;
  }
  .event-list {
    flex: 1; background: var(--event-blue);
    display: flex; flex-direction: column; justify-content: center; gap: 12px;
    padding: 16px 22px;
  }
  .event-list .entry p { font-size: 15.5px; line-height: 1.3; }
  .event-title { font-weight: 700; }
  .event-date-strong { font-weight: 700; }
</style>
</head>
<body>
<main class="sheet">

  <section class="card tour-card" aria-label="Pedal Vista Treks tour card">
    <header class="tour-head">
      <span class="brand-dot"></span>
      <span class="brand-name">Pedal Vista<br>Treks</span>
    </header>
    <p class="tour-tagline">Fully supported bike tours. Discover the hidden gems on two wheels</p>
    <div class="tour-list">
      <div class="listing">
        <p class="listing-name">Heart of Colorado</p>
        <p class="listing-date">June 26 - July 2, 2016</p>
      </div>
      <div class="listing">
        <p class="listing-name">Colorado Front Range Tour</p>
        <p class="listing-date">August 14-20, 2016</p>
      </div>
      <div class="listing">
        <p class="listing-name">Cape Cod Tour</p>
        <p class="listing-date">October 9 -15, 2016</p>
      </div>
      <div class="listing">
        <p class="listing-name">Florida Key Tours</p>
        <p class="listing-date">November 6-12, 2016 &amp;<br>December 4-10, 2016</p>
      </div>
    </div>
  </section>

  <section class="card event-card" aria-label="KQR Venture event card">
    <header class="event-head">
      <span class="brand-dot"></span>
      <span class="brand-name">KQR<br>Venture</span>
    </header>
    <p class="event-tagline">Trail Spoke Series:<br>Cycling camps for youth</p>
    <div class="event-list">
      <div class="entry">
        <p>Mountain Bike Camp</p>
        <p class="event-date-strong">July 8-10, 2016</p>
      </div>
      <div class="entry">
        <p>Cyclocross Camp</p>
        <p class="event-date-strong">August 26-28, 2016</p>
        <p class="event-title">Trailspokeseries.org</p>
      </div>
      <div class="entry">
        <p class="event-title">Summit Century Ride</p>
        <p>June 18, 2016</p>
        <p>Summitcenturyride.com</p>
      </div>
      <div class="entry">
        <p class="event-title">Front Range Park Loop Challenge</p>
        <p>July 30, 2016</p>
        <p>Parkloopride.com</p>
      </div>
      <div class="entry">
        <p class="event-title">Quirky Wheel Ride</p>
        <p>September 11, 2016</p>
        <p>quirkywheelride.com</p>
      </div>
    </div>
  </section>

</main>
</body>
</html>
```